Fresh, modern, fun business card for pediatric dental practice

Need a business card for fresh, modern, fun pediatric dental practice

Clean look that matches our website's font and colors

We prefer the look of curved corners on business cards

Target Market(s)

parents (mothers) of young children, professionals, mid-high class

Industry/Entity Type

Dental

Contact Information for Business Card

Maplebrook Pediatric Dentistry
482 Quarry Lane
Suite 517
Fernhollow, PA 17990
717.555.0193
www.maplebrookkidsdental.example

Mei-Ran Tsai, DMD
Corinne Walbeck, DMD
(we are working on our email address, but we would like that on the card as well)

Font styles to use
Sans Serif

Requirements
Must have
• All info; we would also like to make cards for individual staff members
• colors from our website and color palatte, attatched
• use same font and design as website for branding
Nice to have
• clean, simple card that has a pop of color
• we would like to see a few designs with our tag line "where smiles get brighter"
• we are not sure if we want to have it on there or not
• we would like to see a few designs incorporating the ribbon graphic on our website where the word WELCOME is

```html
<!DOCTYPE html>
<html lang="en">
<head>
<meta charset="utf-8">
<title>Maplebrook Pediatric Dentistry – Business Card</title>
<link rel="stylesheet" href="https://fonts.googleapis.com/css2?family=Roboto:wght@400;500&family=Roboto+Condensed:wght@700&display=swap">
<style>
  :root {
    --stage: #2b2b2b;
    --paper: #f3f3f3;
    --sun: #efb426;
    --berry: #c8338a;
    --ink: #4a4a4a;
    --rule: #c9c9c9;
    --white: #ffffff;
  }
  * { box-sizing: border-box; margin: 0; padding: 0; }
  html, body {
    width: 1200px; height: 960px; overflow: hidden;
    background: var(--stage);
    font-family: "Roboto", Arial, sans-serif;
  }
  .card {
    position: absolute;
    width: 600px; height: 343px;
    border-radius: 22px;
    overflow: hidden;
    box-shadow: 0 3px 8px rgba(0,0,0,.45);
  }
  .card--front { left: 314px; top: 113px; background: var(--paper); }
  .card--back  { left: 311px; top: 472px; background: var(--sun); }

  .wave { position: absolute; left: 0; top: 0; width: 600px; height: 343px; }

  .brand {
    position: absolute; left: 40px; top: 92px; width: 265px;
    text-align: center; color: var(--sun); font-weight: 500;
  }
  .brand__dot {
    display: block; width: 34px; height: 34px; margin: 0 auto 12px;
    border-radius: 50%; background: var(--sun);
  }
  .brand__name { display: block; font-size: 38px; line-height: 1; letter-spacing: .5px; }
  .brand__sub  { display: block; font-size: 17px; line-height: 1.5; margin-top: 4px; letter-spacing: .5px; }

  .divider {
    position: absolute; left: 311px; top: 74px; width: 1px; height: 172px;
    background: var(--rule);
  }

  .contact { position: absolute; left: 337px; top: 78px; }
  .contact__doctor {
    font-family: "Roboto Condensed", "Arial Narrow", sans-serif;
    font-weight: 700; font-size: 21px; line-height: 24px; color: var(--sun);
  }
  .contact__address {
    margin-top: 8px; font-style: normal;
    font-size: 14.5px; line-height: 18px; color: var(--ink);
  }
  .contact__phone {
    display: flex; align-items: center; gap: 6px;
    margin-top: 11px; font-size: 14.5px; color: var(--ink);
  }
  .contact__phone svg { width: 13px; height: 13px; fill: var(--sun); }

  .website {
    position: absolute; left: 0; width: 100%;
    text-align: center; color: var(--white);
    font-size: 13.5px; letter-spacing: 3.2px;
  }
  .card--front .website { top: 313px; }
  .card--back  .website { top: 294px; }

  .back-mark {
    position: absolute; left: 0; top: 70px; width: 100%;
    text-align: center; color: var(--white); font-weight: 500;
  }
  .back-mark__dot {
    display: block; width: 110px; height: 110px; margin: 0 auto 22px;
    border-radius: 50%; background: var(--white);
  }
  .back-mark__name { font-size: 30px; letter-spacing: .5px; }
</style>
</head>
<body>

<section class="card card--front" aria-label="Business card front">
  <svg class="wave" viewBox="0 0 600 343" aria-hidden="true">
    <path fill="var(--sun)" d="M0,310 C110,290 250,306 360,306 C460,306 540,290 600,262 L600,343 L0,343 Z"/>
    <path fill="var(--berry)" d="M8,300 C120,272 260,287 360,291 C460,294 540,276 590,256 C540,284 460,300 360,300 C250,300 110,286 8,302 Z"/>
  </svg>

  <div class="brand">
    <span class="brand__dot"></span>
    <span class="brand__name">Maplebrook</span>
    <span class="brand__sub">Pediatric Dentistry</span>
  </div>

  <div class="divider"></div>

  <div class="contact">
    <p class="contact__doctor">Mei-Ran Tsai, DMD</p>
    <p class="contact__doctor">Corinne Walbeck, DMD</p>
    <address class="contact__address">
      Maplebrook Pediatric Dentistry<br>
      482 Quarry Lane<br>
      Suite 517<br>
      Fernhollow, PA 17990
    </address>
    <p class="contact__phone">
      <svg viewBox="0 0 24 24" aria-hidden="true"><path d="M6.6 10.8c1.4 2.8 3.8 5.1 6.6 6.6l2.2-2.2c.3-.3.7-.4 1-.2 1.1.4 2.3.6 3.6.6.6 0 1 .4 1 1V20c0 .6-.4 1-1 1C10.6 21 3 13.4 3 4c0-.6.4-1 1-1h3.5c.6 0 1 .4 1 1 0 1.3.2 2.5.6 3.6.1.3 0 .7-.2 1z"/></svg>
      717.555.0193
    </p>
  </div>

  <p class="website">www.maplebrookkidsdental.example</p>
</section>

<section class="card card--back" aria-label="Business card back">
  <div class="back-mark">
    <span class="back-mark__dot"></span>
    <span class="back-mark__name">Maplebrook</span>
  </div>
  <p class="website">www.maplebrookkidsdental.example</p>
</section>

</body>
</html>
```